Health and Fitness Club requires a stunning and simple website

We are a health and fitness club based in Dubai, when we launch we will be the biggest club in the country, we will also have the 2 largest activity rooms in the country, we are setting a new standard in the industry by offering one thing, our attitude.

Our attitude means the following:
unlike other clubs we have no hidden charges or fees
our members can join daily, monthly, 6 months or annually
our service and facility are comparable to 5* hotel gyms
our equipment is second to none
our space is the biggest in the country
we do not force our members to use our in-house personal trainers - you can bring your own and we will not charge them entry!
we will have a cutting edge brawnmesh box in our gym with classes by the best trainers in the country
we will be providing free-lance personal trainers a platform to engage customers, grow their business and even use our activity rooms for classes

Basically we will be a gym like no other, simply because we are gym people and we hate the restrictive practices and hidden charges by other gyms, so we are making our own gym which focuses on quality and service.

All of this has to be communicated in the style of the website, the colors of the website we want to be limited to the logo colors as this will be the same theme running throughout the gym.

The landing page of the website HAS to incorporate elements from our social media presences, this basically is the usual, chirplo, snapvault, kinwall. We can have these as a sidebar, the centre of the page should display the latest article from our blog (also on the website) Also we need to have a calendar for activities and classes on the front page. The menu should have links to the following:
Latest News
About us
Team
Gallery
Membership
Classes
Member Log In
Contact Us
Location

The style of the website has to be similar to the logo, particularly in terms of the fonts used.

```html
<!DOCTYPE html>
<html lang="en">
<head>
<meta charset="utf-8">
<title>Corevault Fitness</title>
<link href="https://fonts.googleapis.com/css2?family=Open+Sans:ital,wght@0,400;0,600;0,700;1,400&family=Raleway:wght@400;500&family=Anton&display=swap" rel="stylesheet">
<style>
:root{
  --red:#c8000c;
  --red-dark:#a5000a;
  --red-light:#e01a22;
  --ink:#2e2e2e;
  --muted:#555;
  --rule:#e2e2e2;
  --footer:#2b2b2b;
  --white:#fff;
}
*{box-sizing:border-box;margin:0;padding:0}
html,body{width:929px;height:1200px;overflow:hidden;background:var(--white)}
body{position:relative;font-family:"Open Sans",sans-serif;color:var(--ink)}
.abs{position:absolute}
a{color:inherit;text-decoration:none}

.util-links{top:10px;right:52px;font-size:11px;color:#777;letter-spacing:.3px}
.util-links span{margin:0 6px;color:#aaa}
.phone{top:46px;right:46px;font-size:21px;color:#444;display:flex;align-items:center;gap:4px}

.main-nav{top:86px;left:0;width:929px;height:41px;background:linear-gradient(var(--red-light),var(--red-dark));}
.main-nav ul{list-style:none;display:flex;height:100%;position:absolute}
.main-nav li{display:flex;align-items:center;padding:0 22px;color:var(--white);font-weight:700;font-size:13.5px;border-right:1px solid rgba(0,0,0,.18)}
.main-nav li:last-child{border-right:0}
.nav-left{left:0;padding-left:0}
.nav-left li:first-child{padding-left:53px}
.nav-right{right:0}
.nav-right li:first-child{border-left:0}
.nav-right li:last-child{padding-right:53px}

.brand{top:40px;left:407px;width:116px;height:128px;background:var(--white);border-radius:8px;display:flex;flex-direction:column;align-items:center;justify-content:center;gap:8px;box-shadow:0 2px 6px rgba(0,0,0,.25)}
.brand-dot{width:34px;height:34px;border-radius:50%;background:var(--red)}
.brand-name{font-family:"Open Sans",sans-serif;font-weight:700;font-size:13px;color:var(--red);text-transform:uppercase;letter-spacing:.5px;text-align:center;line-height:1.2}

.hero{top:127px;left:0;width:929px;height:358px;background:linear-gradient(180deg,#dfe6ee 0%,#b9c6d3 45%,#6f7e8c 80%,#2f9fd8 100%)}
.hero-caption{top:125px;left:188px;width:549px;height:119px;background:rgba(40,40,40,.82);border-radius:4px;text-align:center;color:var(--white);font-family:"Anton",sans-serif;line-height:1}
.hero-caption .l1{font-size:44px;margin-top:20px;letter-spacing:.3px}
.hero-caption .l2{font-size:37px;margin-top:4px}
.dots{top:336px;left:436px;display:flex;gap:3px}
.dots i{width:11px;height:11px;border-radius:50%;background:var(--white);display:block}

.intro{top:512px;left:0;width:929px;text-align:center}
.intro h1{font-family:"Raleway",sans-serif;font-weight:400;font-size:27px;letter-spacing:.8px;color:#222}
.intro p{font-family:"Raleway",sans-serif;font-size:11.4px;color:#444;margin-top:5px;line-height:16px;letter-spacing:.2px}
.rule{left:45px;width:838px;height:1px;background:var(--rule)}

.social{top:514px;left:892px;width:37px;height:94px;background:#f1f1f1;border:1px solid #e3e3e3;border-right:0;border-radius:4px 0 0 4px;display:flex;flex-direction:column;align-items:center;justify-content:space-around;padding:3px 0}
.social a{font-size:7px;font-weight:600;color:#444;display:flex;flex-direction:column;align-items:center;gap:1px}
.social a i{width:14px;height:14px;background:#3a5a98;display:block;border-radius:2px}

.col-title{font-size:19px;color:var(--red);font-weight:400;text-transform:uppercase;top:645px}
.why-photo{top:676px;left:45px;width:258px;height:105px;background:linear-gradient(180deg,#f4f4f6,#d9d9e2 70%,#b7a6d6)}
.why-sub{top:787px;left:45px;font-size:14px;color:#333}
.why-text{top:811px;left:45px;width:262px;font-size:10px;line-height:18px;color:#444}

.article{left:343px;display:flex;gap:9px;width:270px}
.article .thumb{width:70px;height:55px;flex:none}
.article h3{font-size:12px;font-weight:400;color:#333}
.article p{font-size:9.4px;line-height:15px;color:#666;margin-top:1px}

.cal{top:676px;left:643px;width:226px;border:1px solid #ddd;border-radius:4px 4px 0 0;overflow:hidden}
.cal-head{height:31px;background:#222;color:var(--white);display:flex;align-items:center;justify-content:space-between;padding:0 10px;font-size:12.5px}
.cal table{width:100%;border-collapse:collapse;table-layout:fixed}
.cal th{background:var(--red);color:var(--white);font-weight:400;font-size:11.5px;height:24px}
.cal td{text-align:center;height:25.3px;font-size:12px;border:1px solid #e3e3e3;color:#222}
.cal td.out{color:#aaa}
.cal td.today{background:#222;color:var(--white)}

.say-title{top:960px;left:0;width:929px;text-align:center;font-size:19px;color:#222}
.quote{top:996px;width:385px;font-size:10.4px;font-style:italic;line-height:18px;color:#333;padding-left:20px}
.quote b{position:absolute;left:0;top:-8px;font-size:26px;font-style:normal;color:#333;font-family:Georgia,serif}
.quote .by{font-style:normal;font-size:12px;color:var(--red);margin-top:7px}

.footer{top:1108px;left:0;width:929px;height:92px;background:var(--footer);color:#eee}
.footer nav{position:absolute;top:23px;left:49px;font-size:12px}
.footer nav span{margin:0 7px;color:#999}
.footer small{position:absolute;top:53px;left:50px;font-size:10.4px;color:#aaa}
</style>
</head>
<body>

<div class="abs util-links"><a href="#">MEMBER LOG IN</a><span>|</span><a href="#">CONTACT US</a><span>|</span><a href="#">LOCATION</a></div>
<div class="abs phone">
  <svg width="14" height="20" viewBox="0 0 14 20"><path d="M4 1 L7 5 L5 7 Q6 11 9 14 L11 12 L14 15 L11 19 Q2 16 1 4 Z" fill="#bbb"/></svg>
  555.014.2270
</div>

<nav class="abs main-nav">
  <ul class="nav-left"><li>LATEST NEWS</li><li>ABOUT US</li><li>TEAM</li></ul>
  <ul class="nav-right"><li>GALLERY</li><li>MEMBERSHIP</li><li>CLASSES</li></ul>
</nav>

<div class="abs brand">
  <span class="brand-dot"></span>
  <span class="brand-name">Corevault<br>Fitness</span>
</div>

<section class="abs hero" role="img" aria-label="Women stretching on blue mats in a bright fitness studio">
  <div class="abs hero-caption">
    <div class="l1">BIGGEST HEALTH &amp; FITNESS</div>
    <div class="l2">CLUB IN THE COUNTRY</div>
  </div>
  <div class="abs dots"><i></i><i></i><i></i><i></i></div>
</section>

<section class="abs intro">
  <h1>INTEGER ORCI TRISTIQUE VITAE CONSEQUAT</h1>
  <p>MAECENAS PLACERAT NISL AT CONSEQUAT RHONCUS SEM NUNC GRAVIDA JUSTO QUIS ELEIFEND ARCU VELIT QUIS LACUS MORBI<br>MAGNA MAGNA TINCIDUNT A MATTIS NON IMPERDIET VITAE TELLUS SED ODIO EST AUCTOR AC SOLLICITUDIN IN CONSEQUAT</p>
</section>

<aside class="abs social">
  <a href="#"><i></i>kinwall</a>
  <a href="#"><i style="background:#3fb6e6"></i>chirplo</a>
  <a href="#"><i style="background:#6b5443"></i>snapvault</a>
</aside>

<div class="abs rule" style="top:608px"></div>

<h2 class="abs col-title" style="left:45px">WHY CHOOSE US</h2>
<div class="abs why-photo" role="img" aria-label="Smiling woman holding purple dumbbells"></div>
<div class="abs why-sub">Mauris vel lacus vitae felis vestibulum</div>
<p class="abs why-text">volutpat Etiam est nunc venenatis in tristique eu imperdiet ac nisl Cum sociis natoque penatibus et magnis dis parturient montes nascetur ridiculus mus In iaculis facilisis massa Etiam eu urna</p>

<h2 class="abs col-title" style="left:343px">LATEST ARTICLES</h2>
<article class="abs article" style="top:677px">
  <div class="thumb" role="img" aria-label="Woman with a water bottle in the gym" style="background:linear-gradient(#f0f0f0,#c9c4d6)"></div>
  <div><h3>Article Tittle here</h3><p>nascetur ridiculus mus In iaculis facilisis massa Etiam eu urna Sed porta Suspend-isse quam leo molestie sed luctus</p></div>
</article>
<article class="abs article" style="top:750px">
  <div class="thumb" role="img" aria-label="People training on treadmills" style="background:linear-gradient(#dfe3e6,#8a9098)"></div>
  <div><h3>Article Tittle here</h3><p>nascetur ridiculus mus In iaculis facilisis massa Etiam eu urna Sed porta Suspend-isse quam leo mole</p></div>
</article>
<article class="abs article" style="top:828px">
  <div class="thumb" role="img" aria-label="Group fitness class with colourful outfits" style="background:linear-gradient(#3a7fd0,#e6e6ee 60%,#5c8ad4)"></div>
  <div><h3>Article Tittle here</h3><p>nascetur ridiculus mus In iaculis facilisis massa Etiam eu urna Sed porta Suspend-isse quam leo mole</p></div>
</article>

<h2 class="abs col-title" style="left:643px">CALENDAR &amp; EVENTS</h2>
<div class="abs cal">
  <div class="cal-head"><span>&#9664;</span><span>FEBURARY 2014</span><span>&#9654;</span></div>
  <table>
    <tr><th>Su</th><th>Mo</th><th>Tu</th><th>We</th><th>Th</th><th>Fr</th><th>Sa</th></tr>
    <tr><td class="out">28</td><td class="out">29</td><td class="out">30</td><td class="out">31</td><td>1</td><td>2</td><td>3</td></tr>
    <tr><td>4</td><td>5</td><td>6</td><td>7</td><td>8</td><td>9</td><td>10</td></tr>
    <tr><td>11</td><td>12</td><td>13</td><td>14</td><td>15</td><td>16</td><td>17</td></tr>
    <tr><td>18</td><td>19</td><td class="today">20</td><td>21</td><td>22</td><td>23</td><td>24</td></tr>
    <tr><td>25</td><td>26</td><td>27</td><td>28</td><td></td><td></td><td class="out">1</td></tr>
    <tr><td class="out">2</td><td class="out">3</td><td class="out">4</td><td class="out">5</td><td class="out">6</td><td class="out">7</td><td class="out">8</td></tr>
  </table>
</div>

<div class="abs rule" style="top:927px"></div>

<h2 class="abs say-title" style="font-weight:400">WHAT OUR CUSTOMER SAY</h2>
<blockquote class="abs quote" style="left:62px">
  <b>&ldquo;</b>
  Suspendisse vulputate aliquam dui Nulla elementum dui ut&nbsp; augue Aliquam vehicula mi at mauris Maecenas placerat nisl at consequat rhoncus sem nunc gravida justo quis eleifend arcu velit quis lacus Morbi m
  <div class="by">By Author Name</div>
</blockquote>
<blockquote class="abs quote" style="left:464px">
  <b>&ldquo;</b>
  Suspendisse vulputate aliquam dui Nulla elementum dui ut&nbsp; augue Aliquam vehicula mi at mauris Maecenas placerat nisl at consequat rhoncus sem nunc gravida justo quis eleifend arcu velit quis lacus
  <div class="by">By Author Name</div>
</blockquote>

<footer class="abs footer">
  <nav>Latest News<span>|</span>About us<span>|</span>Team<span>|</span>Gallery<span>|</span>Membership<span>|</span>Classes<span>|</span>Member Log In<span>|</span>Contact Us<span>|</span>Location</nav>
  <small>&copy; 2014 Company Name.&nbsp; All right reserved.&nbsp; Term of Use</small>
</footer>

</body>
</html>
```